FCL Sign 24”x60”

We need a design for our FCL sign (24”x60”) that is going next to a table (attached is an image of the sign)

I'd like the color scheme to royal blue in the website below and I've attached a few of our school logos.

It should have the colors and simple FCL logo of this tablecloth https://market.fclgoods.net/listings.lasso?c_id=Tablecloths&-session=KI_Clients:4QD8372R205hw9L71ZpNW3K418Z

The most important thing is the words pop and is easy to read from far away.

Bellmere FCL

What do we do?
Help at school events
Support our school and students
Organize fundraising events
Have fun together!

Questions? Email FCLBellmere@mailbrook.net

Get text updates - Text @bellmerefcl to the number 74626

Target Market(s)

Parents of Elementary School Students

Industry/Entity Type

Education

Font styles to use
Sans Serif

Colors

Designer to choose colors to be used in the design.

Requirements
Must have
• Clear words that pop- easy to read

```html
<!DOCTYPE html>
<html lang="en">
<head>
<meta charset="UTF-8">
<title>Bellmere FCL Banner</title>
<link rel="stylesheet" href="https://fonts.googleapis.com/css2?family=Open+Sans:wght@600;700;800&display=swap">
<style>
  :root {
    --navy: #1f2a6b;
    --red: #c40006;
    --white: #ffffff;
    --sky: #bdeff0;
    --page: #e6e6e8;
  }
  * { margin: 0; padding: 0; box-sizing: border-box; }
  html, body { width: 1200px; height: 1200px; overflow: hidden; }
  body {
    background: var(--page);
    font-family: "Open Sans", Arial, sans-serif;
    position: relative;
  }
  .banner {
    position: absolute;
    left: 379px; top: 40px;
    width: 441px; height: 1120px;
    overflow: hidden;
    box-shadow: 0 6px 24px rgba(0,0,0,0.18);
  }
  .banner-art { position: absolute; inset: 0; width: 441px; height: 1120px; }
  .logo-mark {
    position: absolute; left: 70px; top: 60px;
    width: 301px; height: 230px;
    display: flex; flex-direction: column; align-items: center; justify-content: center; gap: 16px;
  }
  .logo-dot { width: 110px; height: 110px; border-radius: 50%; background: var(--navy); }
  .logo-name { color: var(--navy); font-weight: 800; font-size: 34px; line-height: 1; }
  .org-name, .org-type {
    position: absolute; left: 0; width: 100%; text-align: center;
    font-weight: 800; line-height: 1;
  }
  .org-name { top: 318px; font-size: 64px; color: var(--navy); letter-spacing: -0.5px; }
  .org-type { top: 390px; font-size: 70px; color: var(--red); }
  .what-we-do {
    position: absolute; left: 52px; top: 578px;
    color: var(--white); font-weight: 700; white-space: nowrap;
  }
  .what-we-do .lead { font-size: 28px; }
  .what-we-do .big { font-size: 52px; font-weight: 800; letter-spacing: -0.5px; }
  .heading-bar { position: absolute; left: 52px; top: 650px; width: 53px; height: 6px; border-radius: 3px; background: linear-gradient(90deg, var(--white) 30%, var(--navy) 30%); }
  .duty-list { position: absolute; left: 52px; top: 670px; list-style: none; }
  .duty-list li {
    color: var(--white); font-weight: 700; font-size: 20px; line-height: 34.5px;
    display: flex; align-items: center; gap: 7px;
  }
  .duty-list li::before { content: "\203A"; font-size: 26px; font-weight: 800; line-height: 1; margin-top: -4px; }
  .contact {
    position: absolute; left: 0; top: 895px; width: 100%;
    text-align: center; color: var(--white);
  }
  .contact .ask { font-size: 38px; font-weight: 800; line-height: 46px; }
  .contact .email { font-size: 24px; font-weight: 600; line-height: 40px; }
  .contact .updates { font-size: 30px; font-weight: 800; line-height: 44px; }
  .contact .how { font-size: 21px; font-weight: 700; line-height: 30px; }
</style>
</head>
<body>
  <div class="banner">
    <svg class="banner-art" viewBox="0 0 477 1212" preserveAspectRatio="none" aria-hidden="true">
      <defs>
        <linearGradient id="sky" x1="0" y1="0" x2="1" y2="1">
          <stop offset="0" stop-color="#ffffff"/>
          <stop offset="0.55" stop-color="#d7f5f5"/>
          <stop offset="1" stop-color="#ffffff"/>
        </linearGradient>
        <linearGradient id="fade" x1="0" y1="0" x2="0" y2="1">
          <stop offset="0" stop-color="#fff" stop-opacity="0"/>
          <stop offset="1" stop-color="#fff" stop-opacity="1"/>
        </linearGradient>
        <linearGradient id="silver" x1="0" y1="1" x2="1" y2="0">
          <stop offset="0" stop-color="#8d8d92"/>
          <stop offset="0.45" stop-color="#ffffff"/>
          <stop offset="0.7" stop-color="#c9c9cc"/>
          <stop offset="1" stop-color="#7e7e84"/>
        </linearGradient>
      </defs>
      <rect class="sky-wash" width="477" height="620" fill="url(#sky)"/>
      <rect class="sky-fade" y="260" width="477" height="360" fill="url(#fade)"/>
      <polygon class="navy-stripe" points="0,587 477,466 477,478 0,642" fill="#1f2a6b"/>
      <polygon class="red-field" points="0,642 477,478 477,862 0,987" fill="#c40006"/>
      <polygon class="silver-swoosh" points="0,978 477,812 477,856 0,988" fill="url(#silver)"/>
      <polygon class="navy-field" points="0,990 477,864 477,1212 0,1212" fill="#1f2a6b"/>
      <line class="red-edge" x1="0" y1="989" x2="477" y2="863" stroke="#c40006" stroke-width="3"/>
    </svg>

    <div class="logo-mark">
      <span class="logo-dot"></span>
      <span class="logo-name">Bellmere Lions</span>
    </div>

    <h1 class="org-name">Bellmere</h1>
    <div class="org-type">FCL</div>

    <h2 class="what-we-do"><span class="lead">What do </span><span class="big">WE DO?</span></h2>
    <span class="heading-bar"></span>
    <ul class="duty-list">
      <li>Help at school events</li>
      <li>Support our school and students</li>
      <li>Organize fundraising events</li>
      <li>Have fun together!</li>
    </ul>

    <div class="contact">
      <p class="ask">Questions?</p>
      <p class="email">FCLBellmere@mailbrook.net</p>
      <p class="updates">Get text updates</p>
      <p class="how">Text @bellmerefcl</p>
      <p class="how">to the number 74626</p>
    </div>
  </div>
</body>
</html>
```